Bright Meadow Kitchen Business Cards

We need Business cards development for our expanding business. Our Company BrightMeadowKitchen promotes grain free living through products, services and healthy living concepts. Our Products are:
Non-Grain
Non- GMO
Non- Soy
Gluten-Free
Updates

Project Deadline Extended
Reason: We will need to extend the deadline on our Business Card contest. Thanks, BMK

Industry/Entity Type

Business

```html
<!DOCTYPE html>
<html lang="en">
<head>
<meta charset="utf-8">
<title>Bright Meadow Kitchen – Business Card</title>
<link rel="stylesheet" href="https://fonts.googleapis.com/css2?family=Exo+2:wght@500&family=Open+Sans:wght@400&display=swap">
<style>
  :root {
    --backdrop: #3b3b3d;
    --card: #ffffff;
    --green: #3fae2a;
    --green-light: #8fdc5a;
    --ink: #1d1d1d;
    --icon: #ffffff;
  }
  html, body {
    margin: 0;
    width: 1200px;
    height: 816px;
    overflow: hidden;
    background: var(--backdrop);
  }
  .card {
    position: absolute;
    left: 80px;
    top: 118px;
    width: 1040px;
    height: 580px;
    background: var(--card);
    border-radius: 40px;
    overflow: hidden;
  }
  .side-band {
    position: absolute;
    left: 70px;
    top: 0;
    width: 50px;
    height: 530px;
    border-radius: 0 0 25px 25px;
    background: linear-gradient(180deg, var(--green) 0%, var(--green-light) 45%, var(--green) 100%);
  }
  .side-band svg {
    position: absolute;
    left: 13px;
    width: 24px;
    height: 24px;
    fill: var(--icon);
  }
  .edge-tab {
    position: absolute;
    right: 0;
    top: 200px;
    width: 74px;
    height: 26px;
    background: linear-gradient(90deg, var(--green) 0%, var(--green-light) 100%);
  }
  .identity {
    position: absolute;
    left: 150px;
    top: 70px;
    font-family: "Exo 2", sans-serif;
    font-weight: 500;
    color: var(--ink);
  }
  .identity .person {
    font-size: 30px;
    margin: 0;
    line-height: 1.15;
  }
  .identity .role {
    font-size: 28px;
    letter-spacing: 1px;
    margin: 0;
    line-height: 1.2;
  }
  .contact {
    position: absolute;
    left: 150px;
    font-family: "Open Sans", sans-serif;
    font-size: 25px;
    color: var(--ink);
    line-height: 1.3;
    margin: 0;
  }
  .contact.phone { top: 225px; }
  .contact.online { top: 300px; }
  .contact.address { top: 395px; }
  .brand {
    position: absolute;
    left: 480px;
    top: 80px;
    margin: 0;
    font-family: "Exo 2", sans-serif;
    font-weight: 500;
    font-size: 36px;
    color: var(--ink);
    letter-spacing: 0.5px;
  }
</style>
</head>
<body>
  <div class="card">
    <div class="side-band">
      <svg style="top:92px" viewBox="0 0 24 24"><circle cx="12" cy="8" r="5"/><path d="M2 23c0-6 4.5-9 10-9s10 3 10 9z"/></svg>
      <svg style="top:230px" viewBox="0 0 24 24"><path d="M6.6 10.8a15 15 0 0 0 6.6 6.6l2.2-2.2a1 1 0 0 1 1-.25 11.4 11.4 0 0 0 3.6.57 1 1 0 0 1 1 1V20a1 1 0 0 1-1 1A17 17 0 0 1 3 4a1 1 0 0 1 1-1h3.5a1 1 0 0 1 1 1c0 1.25.2 2.45.57 3.57a1 1 0 0 1-.25 1z"/></svg>
      <svg style="top:304px" viewBox="0 0 24 24"><path d="M2 5h20v14H2z M3 6l9 7 9-7" fill="none" stroke="#fff" stroke-width="2"/></svg>
      <svg style="top:338px" viewBox="0 0 24 24"><circle cx="12" cy="12" r="10" fill="none" stroke="#fff" stroke-width="2"/><path d="M2 12h20M12 2c3 3 3 17 0 20M12 2c-3 3-3 17 0 20" fill="none" stroke="#fff" stroke-width="1.6"/></svg>
      <svg style="top:402px" viewBox="0 0 24 24"><path d="M12 3 1 12h3v9h6v-6h4v6h6v-9h3z"/></svg>
    </div>
    <div class="edge-tab"></div>

    <div class="identity">
      <p class="person">sam rivera</p>
      <p class="role">GENERAL MANAGER</p>
    </div>
    <p class="contact phone">+1 (0222) 45-678-90</p>
    <p class="contact online">hello@brightmeadow.com<br>www.brightmeadow.com</p>
    <p class="contact address">418 Orchard Lane,<br>Fern Valley, USA</p>

    <p class="brand">Bright Meadow Kitchen</p>
  </div>
</body>
</html>
```